Business card - Harbor Crest Builders

Design a business card utilizing the given logo.
colors we like: Black, greys, Teal, blues.
Tri color card, horizontal orientation likely
Logo and name likely best on top.
Info on card:

Dennis Farrow
#8 - 4815 Alder Ridge Blvd.
Surrey, B.C. V3K 2R9

778.555.0193
dennisfarrow@tellmail.ca

Slogan: "Building Dreams"

We are a construction company that specializes in new home construction on the West coast of BC Canada. Open Concepts designs of high end homes.

```html
<!DOCTYPE html>
<html lang="en">
<head>
<meta charset="UTF-8">
<title>Harbor Crest Builders – Business Card</title>
<link href="https://fonts.googleapis.com/css2?family=Roboto:wght@400;500&family=Roboto+Condensed:wght@700&display=swap" rel="stylesheet">
<style>
  :root {
    --stage: #2b2b2b;
    --card-top: #262626;
    --card-bottom: #1a1a1a;
    --lime: #7fd13b;
    --lime-deep: #5fb82e;
    --lime-faint: rgba(127, 209, 59, 0.22);
    --text-light: #e4e4e4;
    --text-grey: #b5b5b5;
    --band-text: #1b1b1b;
  }
  * { margin: 0; padding: 0; box-sizing: border-box; }
  html, body {
    width: 1200px;
    height: 1000px;
    overflow: hidden;
    background: var(--stage);
    font-family: "Roboto", Arial, sans-serif;
  }
  .card {
    position: absolute;
    left: 75px;
    top: 200px;
    width: 1050px;
    height: 600px;
    background: linear-gradient(160deg, var(--card-top), var(--card-bottom));
    overflow: hidden;
  }
  .slogan-band {
    position: absolute;
    left: 0;
    top: 0;
    width: 62px;
    height: 100%;
    background: linear-gradient(180deg, var(--lime), var(--lime-deep));
  }
  .slogan {
    position: absolute;
    left: 31px;
    bottom: 40px;
    transform-origin: 0 0;
    transform: rotate(-90deg) translateY(-50%);
    font-family: "Roboto Condensed", Arial, sans-serif;
    font-weight: 700;
    font-size: 27px;
    letter-spacing: 5px;
    color: var(--band-text);
    white-space: nowrap;
  }
  .brand {
    position: absolute;
    left: 120px;
    top: 70px;
    display: flex;
    align-items: center;
    gap: 30px;
  }
  .brand-dot {
    width: 110px;
    height: 110px;
    border-radius: 50%;
    background: var(--lime);
    flex: none;
  }
  .brand-name {
    font-weight: 400;
    font-size: 62px;
    letter-spacing: 3px;
    line-height: 1.05;
    color: var(--lime);
    text-transform: uppercase;
  }
  .deco-circle {
    position: absolute;
    right: -90px;
    bottom: -80px;
    width: 380px;
    height: 380px;
    border-radius: 50%;
    background: var(--lime-faint);
  }
  .contact {
    position: absolute;
    left: 120px;
    top: 300px;
    color: var(--text-grey);
  }
  .person-name {
    font-size: 36px;
    font-weight: 400;
    letter-spacing: 2px;
    color: var(--lime);
    text-transform: uppercase;
    margin-bottom: 8px;
  }
  .credential {
    font-size: 22px;
    line-height: 1.3;
    color: var(--text-light);
  }
  .credential + .credential { color: var(--text-grey); }
  .reach {
    margin-top: 28px;
    font-size: 23px;
    line-height: 1.35;
    color: var(--text-light);
  }
  .reach .label { color: var(--lime); margin-right: 8px; }
  .address {
    margin-top: 26px;
    font-size: 23px;
    line-height: 1.35;
    color: var(--text-light);
  }
  .address span { display: block; }
  .address span + span { color: var(--text-grey); }
</style>
</head>
<body>
  <section class="card">
    <div class="slogan-band"><span class="slogan">BUILDING DREAMS</span></div>

    <div class="deco-circle"></div>

    <header class="brand">
      <div class="brand-dot"></div>
      <div class="brand-name">Harbor Crest<br>Builders</div>
    </header>

    <div class="contact">
      <h1 class="person-name">Dennis Farrow</h1>
      <p class="credential">HWR Warranted Builder</p>
      <p class="credential">Electrical Engineer - B.A.Sc</p>

      <p class="reach"><span class="label">P:</span>778.555.0193<br><span class="label">E:</span>dennisfarrow@tellmail.ca</p>

      <p class="address">
        <span>#8 - 4815 Alder Ridge Blvd.</span>
        <span>Surrey, B.C. V3K 2R9</span>
      </p>
    </div>
  </section>
</body>
</html>
```